Fahrzeugbeschriftung für Hersteller von Campingzubehör
Perfekt! Genau das was wir uns vorgestellt haben. Vielen Dank
Zielgruppe
Wir sind Hersteller von Campingzubehör, made in Germany! Angesprochen werden sollen, Camper, Händler und Vermieter von Freizeitfahrzeugen. Hier soll ein Sonnensegel kreiert werden, als Werbemaßnahme für die o.g. Zielgruppe. Dieses Sonnensegel soll auf die Einzigartigkeit des Campers wieder spiegeln. Für den schönsten Schatten der Welt!
Campen ist IN! und Individualität wird groß geschrieben. Das Alter der Zielgruppe reicht von 42-80 und legt Wert auf Nachhaltigkeit, Qualität, schätzt den Komfort, aber eben auch das Hobby und die damit verbundene Reiselust.
Aufgabenstellung
Druckformat ist eines 3m breit und 2,2m hoch und 1m breit und 2,2m hoch, Druckvorlage ist dabei. Wichtig ist die HP
www.zeltholmgear.com
Das Banner soll dann aussehen wie dies auf der erste Seite des Flyers

```html
<!DOCTYPE html>
<html lang="de">
<head>
<meta charset="utf-8">
<title>Zeltholm Gear – Sunblocker Banner</title>
<link rel="stylesheet" href="https://fonts.googleapis.com/css2?family=Open+Sans:wght@400;600;700&display=swap">
<style>
  :root {
    --paper: #ffffff;
    --leaf: #9dc34e;
    --sun: #f5ee14;
    --ink: #1e1e1e;
    --brand: #8dbb3a;
    --grass-dark: #5f9a2a;
    --grass-light: #8cc63a;
    --sky: #a8e6e0;
    --tree: #4f6e2c;
  }
  html, body {
    margin: 0;
    padding: 0;
    width: 1200px;
    height: 3429px;
    overflow: hidden;
    background: var(--paper);
    font-family: "Open Sans", Arial, sans-serif;
  }
  .sheet {
    position: relative;
    width: 1200px;
    height: 3429px;
  }
  .banner {
    position: absolute;
    box-shadow: 0 12px 40px rgba(0,0,0,0.28);
    overflow: hidden;
  }
  .banner--wide { left: 45px; top: 84px; width: 1110px; height: 814px; }
  .banner--tall { left: 80px; top: 1077px; width: 1037px; height: 2281px; }
  .banner svg { display: block; }
  .headline { font-weight: 400; fill: var(--ink); }
  .tagline { font-weight: 400; fill: var(--ink); }
  .badge-new { font-weight: 700; fill: var(--sun); }
  .brand-name { font-weight: 600; fill: var(--brand); }
</style>
</head>
<body>
<main class="sheet">

  <section class="banner banner--wide">
    <svg width="1110" height="814" viewBox="0 0 1110 814">
      <defs>
        <linearGradient id="meadowWide" x1="0" y1="0" x2="0" y2="1">
          <stop offset="0" stop-color="var(--tree)"/>
          <stop offset="0.25" stop-color="var(--grass-light)"/>
          <stop offset="1" stop-color="var(--grass-dark)"/>
        </linearGradient>
      </defs>
      <rect class="scene-photo" width="1110" height="814" fill="url(#meadowWide)" role="img" aria-label="Sonnige Wiese mit Bäumen im Hintergrund"/>
      <rect class="product-photo" x="124" y="20" width="902" height="431" fill="#a7b68a" role="img" aria-label="Wohnmobil mit ausgefahrener Markise und bedrucktem Sunblocker mit Hundemotiv"/>
      <path class="swoosh-sun" d="M0,814 Q380,470 1110,422 L1110,452 Q420,510 30,814 Z" fill="var(--sun)"/>
      <path class="swoosh-leaf" d="M30,814 Q420,510 1110,452 L1110,814 Z" fill="var(--leaf)"/>
      <path class="logo-field" d="M749,814 Q830,590 1110,552 L1110,814 Z" fill="var(--paper)"/>
      <text class="badge-new" x="643" y="595" font-size="90">NEU</text>
      <text class="headline" x="426" y="597" font-size="28">INDIVIDUELL</text>
      <text class="headline" x="426" y="640" font-size="28">BEDRUCKBARE</text>
      <text class="headline" x="426" y="683" font-size="28">SUNBLOCKER</text>
      <text class="tagline" x="427" y="727" font-size="22">Für den schönsten</text>
      <text class="tagline" x="427" y="757" font-size="22">Schatten der Welt</text>
      <text class="brand-name" x="972" y="744" font-size="28" text-anchor="middle">Zeltholm Gear</text>
    </svg>
  </section>

  <section class="banner banner--tall">
    <svg width="1037" height="2281" viewBox="0 0 1037 2281">
      <defs>
        <linearGradient id="meadowTall" x1="0" y1="0" x2="0" y2="1">
          <stop offset="0" stop-color="var(--sky)"/>
          <stop offset="0.12" stop-color="var(--sky)"/>
          <stop offset="0.2" stop-color="var(--tree)"/>
          <stop offset="0.3" stop-color="var(--grass-light)"/>
          <stop offset="1" stop-color="var(--grass-dark)"/>
        </linearGradient>
      </defs>
      <rect class="scene-photo" width="1037" height="2281" fill="url(#meadowTall)" role="img" aria-label="Sonnige Wiese mit Bäumen und blauem Himmel"/>
      <rect class="product-photo" x="73" y="323" width="918" height="448" fill="#a7b68a" role="img" aria-label="Wohnmobil mit ausgefahrener Markise und bedrucktem Sunblocker mit Hundemotiv"/>
      <path class="swoosh-sun" d="M0,2281 Q150,1150 1037,858 L1037,918 Q220,1180 37,2281 Z" fill="var(--sun)"/>
      <path class="swoosh-leaf" d="M37,2281 Q220,1180 1037,918 L1037,2281 Z" fill="var(--leaf)"/>
      <path class="logo-field" d="M1037,1077 C780,1250 660,1500 685,1750 C705,2000 850,2180 1037,2281 Z" fill="var(--paper)"/>
      <text class="badge-new" x="359" y="1422" font-size="140">NEU</text>
      <text class="headline" x="215" y="1550" font-size="61">INDIVIDUELL</text>
      <text class="headline" x="215" y="1630" font-size="61">BEDRUCKBARE</text>
      <text class="headline" x="215" y="1710" font-size="61">SUNBLOCKER</text>
      <text class="tagline" x="218" y="1843" font-size="45">Für den schönsten</text>
      <text class="tagline" x="218" y="1902" font-size="45">Schatten der Welt</text>
      <text class="brand-name" x="873" y="1676" font-size="38" text-anchor="middle">Zeltholm Gear</text>
    </svg>
  </section>

</main>
</body>
</html>
```